A design led business card for the construction industry

High-end business card to match logo. White logo on dark grey/off black to the front. Matching dark font on white to back, possibly with logo design again.

We offer construction and project management services to commercial and private clients in the UK. Projetcs range from newbuilds, conversion of listed buildings and refurbishments and extensions of existing homes. Our focus is on quality and attention to detail using the highest skills.

Contact Information for Business Card

Name; Dorian Keble BSc
Position; Project Manager
Mobile; 07962 408 175
Tel; 01632 960457
email; dorian@stonevale.co.uk
web; www.stonevale.co.uk
Address; Fenwold on Marle, KX4 7PW

Colors

Designer to choose only greyscale colors for use in the design.

Requirements
Must have
• To include the below description of the business,

CONSTRUCTION - PROJECT MANAGEMENT
Nice to have
• The posibility of the top back of the card being used as a ruler. So will have a measurement to scale in mm or an architect scale of 1:50
Should not have
• Should not be portrait

```html
<!DOCTYPE html>
<html lang="en">
<head>
<meta charset="utf-8">
<title>Stonevale – Business Card</title>
<link rel="stylesheet" href="https://fonts.googleapis.com/css2?family=Arimo:wght@400;700&display=swap">
<style>
  :root {
    --scene-bg: #2b2624;
    --card: #2a2a2b;
    --ink: #f2f2f2;
    --ink-soft: #d9d9d9;
    --rule: #5a5a5c;
    --metal-dark: #1c1c1d;
    --metal-mid: #8a8a8c;
    --metal-light: #e6e6e8;
  }
  * { box-sizing: border-box; margin: 0; padding: 0; }
  html, body {
    width: 1200px; height: 842px; overflow: hidden;
    background: var(--scene-bg);
    font-family: "Arimo", Arial, sans-serif;
  }
  .sheet {
    width: 1200px; height: 842px;
    display: flex; align-items: center; justify-content: center; gap: 60px;
  }
  .card {
    position: relative;
    width: 520px; height: 336px;
    background: var(--card);
    box-shadow: 0 18px 40px rgba(0,0,0,.55);
    color: var(--ink);
    overflow: hidden;
  }

  /* back side */
  .metal-band {
    position: absolute; left: 0; right: 0; height: 16px;
    background: linear-gradient(90deg, var(--metal-dark) 0%, var(--metal-mid) 30%, var(--metal-light) 50%, var(--metal-mid) 70%, var(--metal-dark) 100%);
  }
  .metal-band--top { top: 0; }
  .metal-band--bottom { bottom: 0; }
  .contact {
    position: absolute; inset: 16px 0;
    display: flex; flex-direction: column; align-items: center; justify-content: center;
    text-align: center;
  }
  .contact__name { font-size: 17px; font-weight: 700; letter-spacing: .3px; }
  .contact__name span { font-weight: 400; }
  .contact__role { font-size: 14px; color: var(--ink-soft); margin-top: 1px; }
  .contact__rule { width: 150px; height: 1px; background: var(--rule); margin: 10px 0; }
  .contact__line { font-size: 14.5px; line-height: 1.25; }
  .contact__line b { font-weight: 700; }
  .contact__address { font-size: 14.5px; }

  /* front side */
  .metal-tab {
    position: absolute; top: 50%; width: 22px; height: 44px; transform: translateY(-50%);
    background: linear-gradient(180deg, var(--metal-dark) 0%, var(--metal-mid) 35%, var(--metal-light) 55%, var(--metal-mid) 80%, var(--metal-dark) 100%);
  }
  .metal-tab--left { left: 0; }
  .metal-tab--right { right: 0; }
  .brand {
    position: absolute; inset: 0;
    display: flex; flex-direction: column; align-items: center; justify-content: center;
  }
  .brand__mark {
    width: 70px; height: 70px; border: 3px solid var(--ink); margin-bottom: 26px;
  }
  .brand__name {
    font-size: 26px; font-weight: 400; letter-spacing: 11px; margin-right: -11px;
  }
  .brand__tagline {
    font-size: 11.5px; letter-spacing: .4px; margin-top: 14px; color: var(--ink);
  }
</style>
</head>
<body>
<main class="sheet">
  <section class="card card--back" aria-label="Card back">
    <div class="metal-band metal-band--top"></div>
    <div class="contact">
      <p class="contact__name">DORIAN KEBLE <span>BSc</span></p>
      <p class="contact__role">Project Manager</p>
      <div class="contact__rule"></div>
      <p class="contact__line"><b>P:</b> 07962 408 175</p>
      <p class="contact__line"><b>M:</b> 01632 960457</p>
      <p class="contact__line"><b>E:</b> dorian@stonevale.co.uk</p>
      <p class="contact__line"><b>W:</b> www.stonevale.co.uk</p>
      <div class="contact__rule"></div>
      <p class="contact__address">Fenwold on Marle, KX4 7PW</p>
    </div>
    <div class="metal-band metal-band--bottom"></div>
  </section>

  <section class="card card--front" aria-label="Card front">
    <div class="metal-tab metal-tab--left"></div>
    <div class="brand">
      <div class="brand__mark"></div>
      <p class="brand__name">STONEVALE</p>
      <p class="brand__tagline">CONSTRUCTION - PROJECT MANAGEMENT</p>
    </div>
    <div class="metal-tab metal-tab--right"></div>
  </section>
</main>
</body>
</html>
```